Cleaning service website design

We need a new nice web design(logo will be the same) for a new cleaning service Company:

Informations about Company and logo you can take from flyers in attachments.

This is a cleaning service Company which have simple rules and we would like to show that(in checklist form) on website:

- What we do and that we're Cleaning Green

- Why us?

- How much(our pricing is simple)

Also we would like to communicate with clients by some nice/big pictures on website and the most important thing is our phone number and short/fast Brimtallow.

Also there should be some space for description about our Company.

Generally all information on main page can be short: about us, about service(what we do), last reviews, tips (for example: Tip of the week) and other can be some introduction to subpage where will be more information.

There will be few subpages like: About us, About our service, Photos(Before and after), Reviews , Tips, FAQ, Contact, Looking for a Job? - most of them will be just text so you can project just one example.

```html
<!DOCTYPE html>
<html lang="en">
<head>
<meta charset="utf-8">
<title>Tidy Haven – House Cleaning</title>
<link href="https://fonts.googleapis.com/css2?family=Source+Sans+3:wght@400;600;700&display=swap" rel="stylesheet">
<style>
:root{
  --green:#6cb84a;
  --green-dark:#4e9a2e;
  --blue:#2aa3dc;
  --blue-dark:#1f6fb6;
  --orange:#f7941d;
  --text:#8a8a8a;
  --heading:#4a4a4a;
  --footer:#2b2b2b;
  --footer-bottom:#1c1c1c;
}
*{margin:0;padding:0;box-sizing:border-box}
html,body{width:1082px;height:1200px;overflow:hidden;background:#fff}
body{font-family:"Source Sans 3",sans-serif;color:var(--text);position:relative}
.abs{position:absolute}
a{color:inherit;text-decoration:none}

.topbar{left:0;top:0;width:1082px;height:29px;background:linear-gradient(#fafafa,#ececec)}
.account{right:136px;top:7px;font-size:11.5px;color:#888}
.account span{margin:0 6px;color:#bbb}

.header{left:0;top:29px;width:1082px;height:98px;background:#f3f3f3}
.brand{left:135px;top:27px;display:flex;align-items:center;gap:8px}
.brand-dot{width:34px;height:34px;border-radius:50%;background:var(--green)}
.brand-name{font-size:24px;font-weight:600;color:var(--green)}
.callout{right:136px;top:13px;text-align:right}
.callout-label{font-size:10.5px;font-weight:600;color:var(--blue-dark)}
.callout-label em{font-style:normal;color:var(--green)}
.callout-phone{font-size:24px;font-weight:700;color:var(--orange);line-height:1;margin-top:1px}
.nav{right:136px;top:68px;display:flex;gap:34px;font-size:10.5px;font-weight:600;color:#777}
.nav a.active{color:var(--green);border-bottom:2px solid var(--green);padding-bottom:2px}

.hero{left:135px;top:127px;width:812px;height:319px;overflow:hidden}
.hero-photo{position:absolute;inset:0;background:linear-gradient(180deg,#6a7a66 0%,#4d6a3a 45%,#5d9a35 100%)}
.hero-worker{position:absolute;left:365px;top:15px;width:230px;height:304px;background:linear-gradient(180deg,rgba(240,225,210,.35),rgba(40,90,180,.45));border-radius:40px 40px 0 0}
.hero-title{left:41px;top:55px;font-size:29px;font-weight:700;color:#fff;line-height:1.2}
.hero-sub{left:41px;top:147px;font-size:17px;font-weight:600;color:#fff}
.hero-sub em{font-style:normal;color:var(--orange)}
.hero-cta{left:42px;top:212px;width:221px;height:51px;display:flex;border-radius:6px;overflow:hidden;box-shadow:0 2px 4px rgba(0,0,0,.25)}
.hero-cta-label{flex:1;background:linear-gradient(#ffc400,#f7890d);color:#5a3300;font-size:15.5px;font-weight:600;display:flex;align-items:center;padding-left:25px}
.hero-cta-arrow{width:51px;background:linear-gradient(#fff,#e5e5e5);display:flex;align-items:center;justify-content:center}

.estimate{left:695px;top:178px;width:193px;height:243px;background:linear-gradient(#fff,#ededed);border-radius:4px;box-shadow:0 3px 8px rgba(0,0,0,.3)}
.estimate-head{height:46px;background:linear-gradient(#3bb6ea,#1f96d3);border-radius:4px 4px 0 0;color:#fff;font-size:17px;font-weight:600;display:flex;align-items:center;padding-left:16px}
.estimate-head em{font-style:normal;color:var(--orange)}
.field{position:absolute;left:15px;width:164px;height:30px;border:1px solid #ccc;background:#fff;border-radius:2px;font-size:9.5px;color:#999;padding:8px 10px}
.submit{position:absolute;left:104px;top:197px;width:75px;height:28px;background:linear-gradient(#7ccb52,#54a732);color:#fff;font-size:11px;font-weight:600;display:flex;align-items:center;justify-content:center;border-radius:2px}

.feature{top:492px;width:256px;height:166px;background:linear-gradient(135deg,#ececec,#fafafa 50%,#eeeeee)}
.feature-title{position:absolute;left:0;right:0;top:19px;text-align:center;font-size:17px;font-weight:600;color:var(--green)}
.feature-text{position:absolute;left:21px;top:49px;font-size:11px;line-height:21px;font-weight:600;color:#999;white-space:nowrap}
.feature-more{position:absolute;left:21px;top:125px;width:54px;height:17px;background:linear-gradient(#6fc43f,#3f8f1f);color:#fff;font-size:10px;font-weight:600;display:flex;align-items:center;justify-content:center;border-radius:2px}
.feature-art{position:absolute}
.art-bottles{left:176px;top:98px;width:54px;height:50px;border-radius:8px;background:linear-gradient(135deg,#6a5cc8,#3a8fd6 60%,#f4b400)}
.art-money{left:166px;top:100px;width:74px;height:48px;border-radius:6px;background:linear-gradient(135deg,#8fd65c,#4fa62a)}
.art-eco{left:178px;top:86px;width:61px;height:61px;border-radius:50%;background:radial-gradient(circle,#86c85a,#4e9a2e)}

.welcome{left:135px;top:712px;width:510px}
.section-title{font-size:20px;color:var(--heading);font-weight:400}
.body-copy{margin-top:14px;font-size:11.5px;line-height:24px;color:#888}
.read-more{display:block;margin-top:12px;font-size:11px;font-weight:600;color:#333}
.divider{left:680px;top:720px;width:1px;height:150px;background:linear-gradient(transparent,#e0e0e0,transparent)}
.press{left:722px;top:712px;width:225px}
.press-link{display:block;margin-top:14px;font-size:13.5px;font-weight:600;color:var(--blue)}
.press .body-copy{margin-top:6px;line-height:23px}

.footer{left:0;top:951px;width:1082px;height:212px;background:var(--footer)}
.footer-col{top:35px;color:#fff}
.footer-col h3{font-size:15px;font-weight:600}
.footer-col ul{list-style:none;margin-top:10px}
.footer-col li{font-size:11px;line-height:21px;font-weight:600}
.newsletter-note{font-size:11px;margin-top:10px;font-weight:600}
.newsletter-form{display:flex;gap:6px;margin-top:10px}
.newsletter-input{width:274px;height:36px;background:#fff;border-radius:2px;color:#333;font-size:11px;font-weight:600;padding:11px 14px}
.newsletter-go{width:38px;height:36px;background:linear-gradient(#ffbe00,#f08a10);color:#fff;font-size:13px;font-weight:700;display:flex;align-items:center;justify-content:center;border-radius:2px}
.socials{left:627px;top:155px;display:flex;gap:9px}
.social{width:21px;height:21px;border-radius:2px}
.footer-brand{right:136px;top:146px;display:flex;align-items:center;gap:6px}
.footer-brand .brand-dot{width:22px;height:22px}
.footer-brand .brand-name{font-size:17px}

.bottombar{left:0;top:1163px;width:1082px;height:37px;background:var(--footer-bottom)}
.copyright{left:135px;top:11px;font-size:10.5px;color:#666}
</style>
</head>
<body>

<div class="abs topbar"></div>
<div class="abs account"><a href="#">Login</a><span>|</span><a href="#">Register</a></div>

<header class="abs header">
  <div class="abs brand"><span class="brand-dot"></span><span class="brand-name">Tidy Haven</span></div>
  <div class="abs callout">
    <div class="callout-label">CALL US FOR A <em>FREE ESTIMATE</em></div>
    <div class="callout-phone">555-014-2277</div>
  </div>
  <nav class="abs nav">
    <a href="#" class="active">HOME</a><a href="#">ABOUT US</a><a href="#">ABOUT OUR SERVICE</a><a href="#">PHOTOS</a><a href="#">REVIEWS</a><a href="#">TIPS</a><a href="#">FAQ</a><a href="#">CONTACT</a>
  </nav>
</header>

<section class="abs hero">
  <div class="hero-photo" role="img" aria-label="Blurred photo of a house and green lawn"></div>
  <div class="hero-worker" role="img" aria-label="Smiling cleaner in a blue apron holding a mop and bucket"></div>
  <h1 class="abs hero-title">Affordably making your<br>life Simpler!</h1>
  <p class="abs hero-sub">Imagine! House cleaning as &nbsp;low as <em>$79</em></p>
  <a href="#" class="abs hero-cta">
    <span class="hero-cta-label">View Our Services</span>
    <span class="hero-cta-arrow"><svg width="20" height="14" viewBox="0 0 20 14"><path d="M2 2l5 5-5 5M11 2l5 5-5 5" fill="none" stroke="#f7941d" stroke-width="2.5"/></svg></span>
  </a>
</section>

<form class="abs estimate">
  <div class="estimate-head">GET A&nbsp;<em>FREE</em>&nbsp;ESTIMATE</div>
  <div class="field" style="top:60px">Full Name</div>
  <div class="field" style="top:101px">Email</div>
  <div class="field" style="top:141px;height:46px">Comments</div>
  <div class="submit">SUBMIT</div>
</form>

<div class="abs feature" style="left:135px">
  <div class="feature-title">Why Us</div>
  <p class="feature-text">Lorem ipsum dolor sit amet consectetur<br>adipiscing elit duis ante ut magna<br>is a dummy text.</p>
  <a href="#" class="feature-more">more</a>
  <div class="feature-art art-bottles" role="img" aria-label="Illustration of cleaning bottles"></div>
</div>
<div class="abs feature" style="left:413px">
  <div class="feature-title">Pricing</div>
  <p class="feature-text">Sed ut parspatisas ante dolore ut magna<br>nisi, Aliquam vestibulum nabi<br>jane, mowla jane.</p>
  <a href="#" class="feature-more">more</a>
  <div class="feature-art art-money" role="img" aria-label="Illustration of a stack of banknotes"></div>
</div>
<div class="abs feature" style="left:690px">
  <div class="feature-title">That We Are Eco</div>
  <p class="feature-text">Aliquam magna nisi tortor ut aliquam elit<br>ante dolore is a standard simply<br>dummy text.</p>
  <a href="#" class="feature-more">more</a>
  <div class="feature-art art-eco" role="img" aria-label="Green eco badge with a sprout"></div>
</div>

<section class="abs welcome">
  <h2 class="section-title">Welcome to Tidy Haven.com</h2>
  <p class="body-copy">Lorem ipsum dolor sit amet consectetur adipiscing elit duis, ante dolore ut aliquam magna nisi is<br>a simply standard dummy text for the typesetting industry worldwide. You can add your own text<br>by replaceing this dummy text. Sed ut parspatisas ante dolore ut aliquam magna nisi is also a dummy<br>text for the typesetting industry.</p>
  <a href="#" class="read-more">Read more...</a>
</section>
<div class="abs divider"></div>
<section class="abs press">
  <h2 class="section-title">Press Releases</h2>
  <a href="#" class="press-link">Sed ut parspatisas ut dolore ante</a>
  <p class="body-copy">Lorem ipsum dolor sit amet consectetur adi piscing elit duis. Sed ut parspatisas ut dolore ante. Magna consectetur vehicualm</p>
  <a href="#" class="read-more" style="margin-top:10px">View more...</a>
</section>

<footer class="abs footer">
  <div class="abs footer-col" style="left:135px">
    <h3>Quick Links</h3>
    <ul><li>Home</li><li>About Us</li><li>About Our Service</li><li>Photos</li><li>Contact</li></ul>
  </div>
  <div class="abs footer-col" style="left:297px">
    <h3>Useful Links</h3>
    <ul><li>Terms of use</li><li>Privacy Policy</li><li>Help Center</li><li>Community</li><li>Login Area</li></ul>
  </div>
  <div class="abs footer-col" style="left:443px">
    <h3>Join Our Community</h3>
    <ul><li>Chatterhub</li><li>Birdline</li><li>Workweb</li></ul>
  </div>
  <div class="abs footer-col" style="left:627px">
    <h3>SignUp For Our Monthly Newsletter</h3>
    <p class="newsletter-note">Subscribe our newsletter &amp; get the latest news &amp; updates</p>
    <div class="newsletter-form">
      <div class="newsletter-input">Email Address</div>
      <div class="newsletter-go">GO</div>
    </div>
  </div>
  <div class="abs socials">
    <span class="social" style="background:#2f5fb3"></span>
    <span class="social" style="background:#3ab3e8"></span>
    <span class="social" style="background:#f2a516"></span>
  </div>
  <div class="abs footer-brand"><span class="brand-dot"></span><span class="brand-name">Tidy Haven</span></div>
</footer>

<div class="abs bottombar">
  <p class="abs copyright">© 2013 by, Tidy Haven. All Rights Reserved.</p>
</div>

</body>
</html>
```